Veldmark Supplies Business Card

Professional business card that stand out to our potential customers. Front and back with clean modern design

Industry/Entity Type

Oil and gas

Contact Information for Business Card

Name, address, website , office phone and cell number

Requirements
Must have
• Editable files for each employee

```html
<!DOCTYPE html>
<html lang="en">
<head>
<meta charset="utf-8">
<title>Veldmark Supplies Business Card</title>
<link href="https://fonts.googleapis.com/css2?family=Montserrat:wght@400;700;800&display=swap" rel="stylesheet">
<style>
  :root {
    --stage: #2b2b2b;
    --card: #161616;
    --red: #ea2027;
    --blue: #0fb1d6;
    --white: #f2f2f2;
    --silver-light: #cfcfcf;
    --silver-dark: #0d0d0d;
  }
  * { box-sizing: border-box; margin: 0; padding: 0; }
  html, body {
    width: 1200px; height: 689px; overflow: hidden;
    background: var(--stage);
    font-family: "Montserrat", sans-serif;
  }
  .canvas { position: relative; width: 1200px; height: 689px; }
  .card {
    position: absolute; top: 190px; width: 540px; height: 310px;
    border-radius: 18px; background: var(--card); overflow: hidden;
  }
  /* Back side */
  .card--back { left: 40px; }
  .back-pattern {
    position: absolute; inset: 0;
    background: linear-gradient(115deg, var(--silver-light) 0%, #8a8a8a 28%, #2a2a2a 55%, var(--silver-dark) 100%);
  }
  .back-mark {
    position: absolute; left: 50%; top: 50%; transform: translate(-50%, -50%);
    display: flex; align-items: center; gap: 8px;
    background: var(--card); padding: 8px 14px; border-radius: 6px;
  }
  .back-mark__square { width: 10px; height: 10px; background: var(--red); }
  .back-mark__name { color: var(--white); font-weight: 800; font-size: 13px; letter-spacing: 0.06em; text-transform: uppercase; }

  /* Front side */
  .card--front { left: 620px; }
  .accent-bar { position: absolute; left: 0; top: 62px; width: 12px; height: 52px; background: var(--red); }
  .identity { position: absolute; left: 34px; top: 58px; }
  .identity__name { font-weight: 700; font-size: 27px; letter-spacing: 0.02em; line-height: 1; }
  .identity__first { color: var(--red); }
  .identity__last { color: var(--blue); }
  .identity__title { color: var(--white); font-size: 14px; margin-top: 8px; }
  .address { position: absolute; left: 34px; top: 140px; color: var(--white); font-size: 13px; line-height: 20px; }
  .contacts { position: absolute; left: 34px; top: 190px; list-style: none; color: var(--white); font-size: 13px; }
  .contacts li { display: flex; align-items: center; gap: 10px; height: 22px; }
  .contacts svg { width: 13px; height: 13px; fill: var(--red); flex: none; }
  .wordmark {
    position: absolute; right: 34px; top: 130px;
    display: flex; align-items: center; gap: 10px;
  }
  .wordmark__square { width: 18px; height: 18px; background: var(--red); }
  .wordmark__name { color: var(--white); font-weight: 800; font-size: 21px; letter-spacing: 0.05em; text-transform: uppercase; }
</style>
</head>
<body>
<main class="canvas">
  <section class="card card--back" aria-label="Card back">
    <div class="back-pattern" role="img" aria-label="Repeating brand emblem pattern fading from silver to black"></div>
    <div class="back-mark">
      <span class="back-mark__square"></span>
      <span class="back-mark__name">Veldmark Supplies</span>
    </div>
  </section>

  <section class="card card--front" aria-label="Card front">
    <div class="accent-bar"></div>
    <div class="identity">
      <h1 class="identity__name"><span class="identity__first">MARCUS</span> <span class="identity__last">HALE</span></h1>
      <p class="identity__title">Managing Director</p>
    </div>
    <p class="address">412 N.Carrow Suite 5<br>Midland, Tx 79701</p>
    <ul class="contacts">
      <li><svg viewBox="0 0 24 24"><path d="M6.6 10.8a15 15 0 0 0 6.6 6.6l2.2-2.2a1 1 0 0 1 1-.25 11.4 11.4 0 0 0 3.6.57 1 1 0 0 1 1 1V20a1 1 0 0 1-1 1A17 17 0 0 1 3 4a1 1 0 0 1 1-1h3.5a1 1 0 0 1 1 1c0 1.25.2 2.45.57 3.57a1 1 0 0 1-.25 1z"/></svg>(555)240-0318</li>
      <li><svg viewBox="0 0 24 24"><path d="M7 1h10a2 2 0 0 1 2 2v18a2 2 0 0 1-2 2H7a2 2 0 0 1-2-2V3a2 2 0 0 1 2-2zm0 3v14h10V4zm5 15.5a1 1 0 1 0 0 2 1 1 0 0 0 0-2z"/></svg>555 987 123</li>
      <li><svg viewBox="0 0 24 24"><path d="M2 5h20v14H2zm2 2v.5l8 5 8-5V7zm0 2.8V17h16V9.8l-8 5z"/></svg>sales@veldmarksupplies.com</li>
      <li><svg viewBox="0 0 24 24"><path d="M12 2a10 10 0 1 0 0 20 10 10 0 0 0 0-20zm6.9 6h-3a15 15 0 0 0-1.3-3.8A8 8 0 0 1 18.9 8zM12 4c.8 1.1 1.5 2.5 1.9 4h-3.8c.4-1.5 1.1-2.9 1.9-4zM4.3 14a8 8 0 0 1 0-4h3.4a16 16 0 0 0 0 4zm.8 2h3a15 15 0 0 0 1.3 3.8A8 8 0 0 1 5.1 16zm3-8h-3a8 8 0 0 1 4.3-3.8A15 15 0 0 0 8.1 8zM12 20c-.8-1.1-1.5-2.5-1.9-4h3.8c-.4 1.5-1.1 2.9-1.9 4zm2.3-6H9.7a14 14 0 0 1 0-4h4.6a14 14 0 0 1 0 4zm.3 5.8a15 15 0 0 0 1.3-3.8h3a8 8 0 0 1-4.3 3.8zm1.7-5.8a16 16 0 0 0 0-4h3.4a8 8 0 0 1 0 4z"/></svg>www.veldmarksupplies.com</li>
    </ul>
    <div class="wordmark">
      <span class="wordmark__square"></span>
      <span class="wordmark__name">Veldmark Supplies</span>
    </div>
  </section>
</main>
</body>
</html>
```